WTF!!! We need a modern professional website for a business litigation law firm.

We need a modern, clean, professional and uncomplicated website for a new business trial and litigation law firm called "Haverlock Trial Firm PLLC". Website must be mobile optimized for iPad and smartphone. The law firm specializes in counseling and representing large corporations, small businesses and entrepreneurs in and out of the courtroom. Lawyers in the firm serve as Florida counsel and trial counsel to organizations facing claims involving product liability, premises liability, professional liability, vehicle and transportation liability, warranty claims, construction defects and delay claims, complex business disputes, commercial litigation and bid disputes in State and Federal Courts. The website is mainly to provide information about the firm, and should include sections describing the firm, identifying the Industries Served and Areas of Practice ," a separate page identifying the "Professionals", a separate page for "Resources & Advisories," and a traveling "Connect With Us" button a site visitor can click on that will launch an email to the Firm's general email account. The website should allow us to easily modify the content on these pages, and let us add/modify links to external information sources. We will not sell anything or take payments through the website. We do need to be able to easily upload and update photographs of attorneys and add new attorneys names/email hyperlinks as the firm grows. We would like to add developments in the law or success stories easily and quickly, such as through a blog page. On the "Connect With Us" page the website should have hyperlinks to email the Firm, and there should be hyperlinks to email each professional on the "Professionals" page. The website should be viewable on mobile devices without distortion. The law firm focuses on trial work and should have some imagery associated with courtrooms, but the overall theme of the site should be modern, clean, and communicate sophistication and strength. The website should be made in Wordpress. We have uploaded logo files for Haverlock Trial Firm.

Target Market(s)

Corporations and companies that are looking for legal representation. Other attorneys/legal industry.

Industry/Entity Type

Legal Industry

Coding

Coded - Design and coding required

Number of Pages Required

1 page

Font styles to use
Sans Serif

Requirements
Must have
• Simple, clean, sophisticated, modern website that includes the logo, watermark of logo, and the elements described above.
Nice to have
• Pictures of city scape, buildings, courtroom, team members.

```html
<!DOCTYPE html>
<html lang="en">
<head>
<meta charset="utf-8">
<title>Haverlock Trial Firm PLLC</title>
<link href="https://fonts.googleapis.com/css2?family=Rubik:wght@400;500;700;800&family=Roboto:wght@400;500;700&display=swap" rel="stylesheet">
<style>
:root{
  --gold:#bf9a53;
  --ink:#0b0b0b;
  --text:#222;
  --muted:#6b6b6b;
  --light:#f1f1f1;
  --white:#fff;
  --footer:#111214;
  --footer-bottom:#050505;
}
*{box-sizing:border-box;margin:0;padding:0}
html,body{width:1200px;height:3672px;overflow:hidden}
body{position:relative;font-family:Roboto,Arial,sans-serif;color:var(--text);background:var(--white)}
.abs{position:absolute}
a{color:inherit;text-decoration:none}

/* top bar */
.topbar{left:0;top:0;width:1200px;height:37px;background:var(--ink);color:#fff;font-size:13px}
.topbar .addr{left:72px;top:11px;display:flex;align-items:center;gap:6px}
.topbar .call{left:631px;top:12px;font-size:12px;font-weight:500}
.topbar .phone{left:846px;top:6px;display:flex;align-items:center;gap:8px;font-family:Rubik,sans-serif;font-size:19px;font-weight:500}
.topbar .social{left:1041px;top:6px;display:flex;gap:6px}
.topbar .social span{width:24px;height:24px;background:#fff;border-radius:2px;display:block}

/* header */
.header{left:0;top:37px;width:1200px;height:85px;background:#fff}
.logo-tab{left:28px;top:37px;width:240px;height:141px;background:#fff;clip-path:polygon(0 0,100% 0,100% 55%,87% 100%,13% 100%,0 55%);z-index:3;display:flex;flex-direction:column;align-items:center;justify-content:center;padding-top:10px}
.logo-name{font-family:Rubik,sans-serif;font-weight:800;font-size:30px;color:var(--ink);letter-spacing:.5px;line-height:1}
.logo-sub{font-family:Rubik,sans-serif;font-weight:800;font-size:14px;color:var(--ink);letter-spacing:4px;margin-top:6px}
.nav{left:323px;top:72px;display:flex;gap:19px;font-size:13px;color:#222}
.nav .active{color:var(--gold)}
.btn-connect{left:946px;top:60px;width:181px;height:40px;background:var(--gold);color:#fff;font-family:Rubik,sans-serif;font-weight:500;font-size:13px;display:flex;align-items:center;justify-content:center;letter-spacing:.3px}

/* hero */
.hero{left:0;top:122px;width:1200px;height:676px;background:linear-gradient(180deg,#4d5766 0%,#8a7a62 22%,#5b6470 45%,#3b4552 70%,#2d3540 100%)}
.hero-title{left:0;top:300px;width:1200px;text-align:center;color:#fff;font-family:Rubik,sans-serif;font-weight:700;font-size:51px;letter-spacing:1px}
.hero-sub{left:300px;top:374px;width:600px;text-align:center;color:#fff;font-size:18px;line-height:1.5}
.hero-btn{left:486px;top:456px;width:229px;height:51px;background:var(--gold);color:#fff;font-family:Rubik,sans-serif;font-weight:500;font-size:16px;display:flex;align-items:center;justify-content:center}
.hero-arrow{top:408px;width:42px;height:42px;border:1.5px solid #fff;border-radius:50%;display:flex;align-items:center;justify-content:center}

/* practice */
.practice{left:111px;top:678px;width:978px;height:285px;background:#fff;box-shadow:0 4px 18px rgba(0,0,0,.12);border-radius:6px;overflow:hidden;z-index:2}
.practice-label{left:0;top:0;width:63px;height:285px;background:var(--ink);display:flex;align-items:center;justify-content:center}
.practice-label span{transform:rotate(-90deg);white-space:nowrap;color:#fff;font-family:Rubik,sans-serif;font-size:28px;font-weight:400}
.practice-label b{font-weight:700}
.practice-grid{left:63px;top:0;width:915px;height:285px;display:grid;grid-template-columns:repeat(4,1fr);grid-template-rows:repeat(2,1fr)}
.practice-item{border-right:1px solid #eee;border-bottom:1px solid #eee;display:flex;flex-direction:column;align-items:center;justify-content:center;text-align:center;gap:12px;font-family:Rubik,sans-serif;font-size:15px;color:#111;text-transform:uppercase;line-height:1.15;padding:0 8px}
.practice-item.raised{box-shadow:0 4px 14px rgba(0,0,0,.15)}

/* section headings */
.sec-head{position:absolute;height:65px}
.sec-head .box{width:100%;height:100%;border:1.5px solid #555;display:flex;align-items:center;justify-content:center;white-space:nowrap;font-family:Rubik,sans-serif;font-size:38px;line-height:1;color:#111}
.sec-head .box b{font-weight:700;margin-right:10px}
.sec-head .tag{position:absolute;left:50%;bottom:-9px;transform:translateX(-50%);white-space:nowrap;padding:0 14px;color:var(--gold);font-family:Rubik,sans-serif;font-size:14px;line-height:16px}

/* who */
.who-lead{left:111px;top:1166px;width:400px;font-size:14px;line-height:1.55;color:#111;font-weight:500}
.who-p{left:111px;width:395px;font-size:14px;line-height:1.6;color:var(--muted)}
.btn-gold{background:var(--gold);color:#fff;font-family:Rubik,sans-serif;font-weight:500;font-size:14px;display:flex;align-items:center;justify-content:center}
.who-img{left:536px;top:1067px;width:664px;height:396px;background:linear-gradient(135deg,#6b5a4e,#c9b8a6 45%,#3b3430)}

/* industries */
.industries{left:0;top:1563px;width:1200px;height:864px;background:var(--light)}
.ind-grid{left:113px;top:1751px;width:974px;height:587px;display:grid;grid-template-columns:repeat(3,1fr);grid-template-rows:repeat(2,1fr)}
.ind-card{position:relative}
.ind-card .strip{position:absolute;right:0;top:0;width:45px;height:100%;background:rgba(18,18,18,.92);display:flex;align-items:center;justify-content:center}
.ind-card .strip span{transform:rotate(-90deg);white-space:nowrap;color:#fff;font-family:Rubik,sans-serif;font-size:17px}

/* speak */
.speak-photo{left:111px;top:2641px;width:472px;height:309px;background:linear-gradient(135deg,#5e6a72,#a48a6c 55%,#6b5846)}
.speak-copy{left:111px;top:2992px;width:410px;font-size:15px;line-height:1.5;color:#333;font-family:Rubik,sans-serif}
.nowin{left:111px;top:3076px;font-family:Rubik,sans-serif;font-weight:500;font-size:25px;color:#111}
.free{left:111px;top:3108px;font-size:13px;color:#555;letter-spacing:.3px}
.bigphone{left:111px;top:3136px;display:flex;align-items:center;gap:12px;color:var(--gold);font-family:Rubik,sans-serif;font-weight:500;font-size:33px}
.vline{left:542px;top:2950px;width:2px;height:242px;background:#1f3350}
.speak-right{left:675px;top:2631px;width:410px;font-size:14px;line-height:1.55;color:var(--muted)}
.contact-box{left:674px;top:2753px;width:415px;height:435px;background:var(--gold)}
.contact-box h3{position:absolute;left:36px;top:34px;color:#fff;font-family:Rubik,sans-serif;font-weight:500;font-size:26px}
.field{position:absolute;left:36px;width:343px;height:34px;background:#fff;font-size:12px;color:#555;padding:10px 11px}
.btn-help{position:absolute;left:36px;top:352px;width:343px;height:44px;background:#000;color:#fff;font-family:Rubik,sans-serif;font-weight:500;font-size:16px;display:flex;align-items:center;justify-content:center}

/* footer */
.footer{left:0;top:3303px;width:1200px;height:311px;background:var(--footer);color:#fff}
.f-logo{position:absolute;left:111px;top:110px;width:190px;text-align:center}
.f-logo .logo-name,.f-logo .logo-sub{color:#fff}
.f-social{position:absolute;left:131px;top:210px;display:flex;gap:10px}
.f-social span{width:30px;height:30px;border-radius:50%;background:#fff;display:block}
.f-social span.on{background:var(--gold)}
.f-col{position:absolute;top:45px}
.f-col h4{font-family:Rubik,sans-serif;font-weight:500;font-size:18px;letter-spacing:.3px}
.f-col h4::after{content:"";display:block;width:60px;height:2px;background:var(--gold);margin-top:10px}
.f-links{margin-top:14px;font-size:12px;line-height:25.5px}
.f-contact{margin-top:12px;font-size:12px}
.f-contact div{display:flex;align-items:center;gap:12px;margin-bottom:16px;line-height:1.6}
.f-contact i{width:26px;height:26px;border-radius:50%;background:#fff;display:flex;align-items:center;justify-content:center;flex:none}
.f-sub p{margin-top:14px;font-size:12px;line-height:1.7;width:240px}
.f-sub .email{margin-top:12px;width:252px;height:34px;border-radius:17px;background:#fff;display:flex;overflow:hidden}
.f-sub .email span{flex:1;font-size:10px;color:#666;padding:11px 14px}
.f-sub .email b{width:48px;background:var(--gold);display:flex;align-items:center;justify-content:center}
.chat{left:1121px;top:3564px;width:36px;height:36px;border-radius:50%;background:var(--gold);display:flex;align-items:center;justify-content:center}
.bottom{left:0;top:3614px;width:1200px;height:58px;background:var(--footer-bottom);color:#fff;font-size:13px}
.bottom .copy{left:111px;top:22px}
.bottom .copy u{font-weight:500}
.bottom .legal{left:877px;top:22px}
</style>
</head>
<body>

<div class="abs topbar">
  <div class="abs addr">
    <svg width="10" height="13" viewBox="0 0 10 13"><path d="M5 0a5 5 0 0 0-5 5c0 4 5 8 5 8s5-4 5-8a5 5 0 0 0-5-5zm0 7a2 2 0 1 1 0-4 2 2 0 0 1 0 4z" fill="#fff"/></svg>
    418 Meridian Street - Suite 120, Alder Springs NY, 10987
  </div>
  <div class="abs call">CALL FOR A FREE CONSULTATION!</div>
  <div class="abs phone">
    <svg width="26" height="26" viewBox="0 0 26 26"><circle cx="13" cy="13" r="12" fill="none" stroke="#fff" stroke-width="1.4"/><path d="M9 7l2.5 0 1 3-1.6 1.2a8 8 0 0 0 3.9 3.9L16 13.5l3 1v2.5a1.5 1.5 0 0 1-1.5 1.5A10.5 10.5 0 0 1 7.5 8.5 1.5 1.5 0 0 1 9 7z" fill="#fff"/></svg>
    (555) 014-2290
  </div>
  <div class="abs social" aria-label="Social links"><span></span><span></span><span></span></div>
</div>

<div class="abs header"></div>
<div class="abs logo-tab"><div class="logo-name">HAVERLOCK</div><div class="logo-sub">TRIAL FIRM</div></div>
<nav class="abs nav">
  <a class="active">Home</a><a>About Us</a><a>Industries</a><a>Areas of Practice</a><a>Professionals</a><a>Resources &amp; Advisories</a><a>Blog</a>
</nav>
<a class="abs btn-connect">CONNECT WITH US</a>

<section class="abs hero" role="img" aria-label="Aerial view of a city skyline at sunset"></section>
<h1 class="abs hero-title">HAVERLOCK TRIAL FIRM</h1>
<p class="abs hero-sub">Lorem ipsum dolor sit amet, consectetur adipiscing elit, sed do eiusmod tempor incididunt ut labore et dolore magna aliqua.</p>
<a class="abs hero-btn">FREE CONSULTATION</a>
<div class="abs hero-arrow" style="left:30px"><svg width="12" height="18" viewBox="0 0 12 18"><path d="M10 1L2 9l8 8" fill="none" stroke="#fff" stroke-width="2"/></svg></div>
<div class="abs hero-arrow" style="left:1127px"><svg width="12" height="18" viewBox="0 0 12 18"><path d="M2 1l8 8-8 8" fill="none" stroke="#fff" stroke-width="2"/></svg></div>

<section class="abs practice">
  <div class="abs practice-label"><span><b>PRACTICE</b> AREAS</span></div>
  <div class="abs practice-grid">
    <div class="practice-item"><svg width="48" height="50" viewBox="0 0 48 50" fill="none" stroke="#1d3a66" stroke-width="2"><rect x="16" y="6" width="16" height="22" rx="2"/><path d="M4 40h14l10 4 14-8" stroke="#bf9a53"/><path d="M20 14h8M20 20h8"/></svg>Product Liability</div>
    <div class="practice-item raised"><svg width="48" height="50" viewBox="0 0 48 50" fill="none" stroke="#1d3a66" stroke-width="2"><rect x="20" y="20" width="22" height="26"/><path d="M8 46V28l8-6 8 6M26 28h4M34 28h4M26 36h4M34 36h4"/><path d="M12 16l10-10" stroke="#bf9a53"/></svg>Commercial Litigation<br>and Bid Disputes</div>
    <div class="practice-item"><svg width="48" height="50" viewBox="0 0 48 50" fill="none" stroke="#1d3a66" stroke-width="2"><rect x="10" y="6" width="28" height="38" rx="2"/><path d="M16 16h16M16 24h16M16 32h10"/><circle cx="34" cy="36" r="6" stroke="#bf9a53"/></svg>Premises Liability</div>
    <div class="practice-item"><svg width="48" height="50" viewBox="0 0 48 50" fill="none" stroke="#1d3a66" stroke-width="2"><circle cx="20" cy="12" r="5"/><rect x="10" y="24" width="22" height="22"/><path d="M15 32h12M21 28v12"/><circle cx="38" cy="10" r="6" stroke="#bf9a53"/></svg>Professional Liability</div>
    <div class="practice-item"><svg width="48" height="50" viewBox="0 0 48 50" fill="none" stroke="#1d3a66" stroke-width="2"><path d="M6 24L24 8l18 16M10 22v22h28V22"/><path d="M16 34l8-6 8 6" stroke="#bf9a53"/></svg>Vehicle and<br>Transportation Liability</div>
    <div class="practice-item"><svg width="48" height="50" viewBox="0 0 48 50" fill="none" stroke="#1d3a66" stroke-width="2"><rect x="10" y="6" width="28" height="26"/><path d="M16 14h4M28 14h4M16 22h4M28 22h4"/><circle cx="16" cy="40" r="4" stroke="#bf9a53"/><circle cx="32" cy="40" r="4" stroke="#bf9a53"/></svg>Warranty Claims</div>
    <div class="practice-item"><svg width="48" height="50" viewBox="0 0 48 50" fill="none" stroke="#1d3a66" stroke-width="2"><rect x="8" y="4" width="26" height="36" rx="2"/><path d="M14 14h14M14 22h10"/><path d="M30 30l8-3 8 3v6c0 5-8 9-8 9s-8-4-8-9z" stroke="#bf9a53"/></svg>Construction Defects<br>and Delay Claims</div>
    <div class="practice-item"><svg width="48" height="50" viewBox="0 0 48 50" fill="none" stroke="#1d3a66" stroke-width="2"><circle cx="24" cy="10" r="5"/><path d="M6 40l10-8h16l10 8" /><rect x="12" y="40" width="24" height="6" stroke="#bf9a53"/></svg>Complex Business<br>Disputes</div>
  </div>
</section>

<!-- who we are -->
<div class="sec-head" style="left:111px;top:1062px;width:326px">
  <div class="box"><span style="margin-right:10px">WHO</span><b style="margin-right:0">WE ARE</b></div>
  <span class="tag" style="background:#fff">Get Jusice For Your Pain &amp; Suffering</span>
</div>
<p class="abs who-lead">Lorem ipsum dolor sit amet, consectetur adipiscing elit, sed do eiusmod tempor incididunt ut labore et dolore magna aliqua. Ut enim ad minim veniam,</p>
<p class="abs who-p" style="top:1244px">Sed ut perspiciatis unde omnis iste natus error sit voluptatem accusantium doloremque laudantium, totam rem aperiam, eaque ipsa quae ab illo inventore veritatis et quasi architecto beatae vitae dicta sunt explicabo.</p>
<p class="abs who-p" style="top:1342px">Nemo enim ipsam voluptatem quia voluptas sit aspernatur aut odit aut fugit, dvoluptatem sequi nesciunt.</p>
<a class="abs btn-gold" style="left:111px;top:1421px;width:156px;height:47px">LEARN MORE</a>
<div class="abs who-img" role="img" aria-label="Business professionals meeting in an office"></div>

<!-- industries -->
<section class="abs industries"></section>
<div class="sec-head" style="left:368px;top:1625px;width:463px">
  <div class="box"><b>INDUSTRIES</b><span>SERVED</span></div>
  <span class="tag" style="background:var(--light)">Haverlock Trial Areas Of Focus</span>
</div>
<div class="abs ind-grid">
  <div class="ind-card" role="img" aria-label="Business team in an office" style="background:linear-gradient(135deg,#8a8f96,#cfcbc4 50%,#5d5a58)"><div class="strip"><span>Investment Funds</span></div></div>
  <div class="ind-card" role="img" aria-label="Official stamping a document" style="background:linear-gradient(135deg,#6f5a46,#d8c7ae 55%,#8a6d4e)"><div class="strip"><span>Public Officials</span></div></div>
  <div class="ind-card" role="img" aria-label="Accountant working with a calculator and charts" style="background:linear-gradient(135deg,#c9cbcf,#eceae6 55%,#9ea3aa)"><div class="strip"><span>Accountants</span></div></div>
  <div class="ind-card" role="img" aria-label="Doctors at a hospital desk" style="background:linear-gradient(135deg,#9ca6b0,#e7e6e4 50%,#5a6470)"><div class="strip"><span>Physicians</span></div></div>
  <div class="ind-card" role="img" aria-label="Financial team reviewing documents" style="background:linear-gradient(135deg,#3b5f70,#c9c4b6 55%,#5e5b4c)"><div class="strip"><span>Financial Services</span></div></div>
  <div class="ind-card" role="img" aria-label="Executives in a boardroom discussion" style="background:linear-gradient(135deg,#4d4f4c,#9f8d78 55%,#3a3834)"><div class="strip"><span>Corporate Executives,</span></div></div>
</div>

<!-- speak -->
<div class="sec-head" style="left:368px;top:2511px;width:463px">
  <div class="box"><b>SPEAK WITH</b><span>AN EXPERT</span></div>
  <span class="tag" style="background:#fff">Contact Our Firm TO Achieve The Justice</span>
</div>
<div class="abs speak-photo" role="img" aria-label="Attorney on a phone call reviewing papers at his desk"></div>
<p class="abs speak-copy">Don't Wait. Contact Us to Get the Help You Deserve From One of the Bes Newyork litigation and transactional work law firm!</p>
<div class="abs nowin">NO WIN &nbsp;. &nbsp;NO FEE!</div>
<div class="abs free">100% FREE CASE EVALUATION</div>
<div class="abs bigphone">
  <svg width="32" height="32" viewBox="0 0 24 24"><path d="M6.6 10.8a15 15 0 0 0 6.6 6.6l2.2-2.2c.3-.3.7-.4 1-.2 1.1.4 2.3.6 3.6.6.6 0 1 .4 1 1V20c0 .6-.4 1-1 1A17 17 0 0 1 3 4c0-.6.4-1 1-1h3.5c.6 0 1 .4 1 1 0 1.3.2 2.5.6 3.6.1.3 0 .7-.2 1z" fill="#bf9a53"/></svg>
  (555) 014-2290
</div>
<div class="abs vline"></div>
<p class="abs speak-right">Sed ut perspiciatis unde omnis iste natus error sit voluptatem accusantium doloremque laudantium, totam rem aperiam, eaque ipsa quae ab illo inventore veritatis et quasi architecto beatae vitae dicta sunt explicabo.</p>
<form class="abs contact-box">
  <h3>Contact Us</h3>
  <div class="field" style="top:85px">Name</div>
  <div class="field" style="top:132px">Email</div>
  <div class="field" style="top:178px">Phone</div>
  <div class="field" style="top:226px;height:104px">Message</div>
  <div class="btn-help">GET HELP NOW!</div>
</form>

<!-- footer -->
<footer class="abs footer">
  <div class="f-logo"><div class="logo-name">HAVERLOCK</div><div class="logo-sub">TRIAL FIRM</div></div>
  <div class="f-social" aria-label="Social links"><span></span><span class="on"></span><span></span><span></span></div>
  <div class="f-col" style="left:387px">
    <h4>QUICK LINKS</h4>
    <div class="f-links">Home<br>About Us<br>Industries Served<br>Areas of Practice<br>Professionals<br>Resources &amp; Advisories<br>Blog</div>
  </div>
  <div class="f-col" style="left:591px">
    <h4>CONTACT US</h4>
    <div class="f-contact">
      <div><i><svg width="12" height="12" viewBox="0 0 24 24"><path d="M6.6 10.8a15 15 0 0 0 6.6 6.6l2.2-2.2c.3-.3.7-.4 1-.2 1.1.4 2.3.6 3.6.6.6 0 1 .4 1 1V20c0 .6-.4 1-1 1A17 17 0 0 1 3 4c0-.6.4-1 1-1h3.5c.6 0 1 .4 1 1 0 1.3.2 2.5.6 3.6.1.3 0 .7-.2 1z" fill="#111"/></svg></i>(555) 014-2290</div>
      <div><i><svg width="12" height="10" viewBox="0 0 12 10"><rect x="0" y="0" width="12" height="10" rx="1" fill="#111"/><path d="M0 1l6 4 6-4" stroke="#fff" fill="none"/></svg></i>info@haverlocktrial.com</div>
      <div><i><svg width="10" height="13" viewBox="0 0 10 13"><path d="M5 0a5 5 0 0 0-5 5c0 4 5 8 5 8s5-4 5-8a5 5 0 0 0-5-5zm0 7a2 2 0 1 1 0-4 2 2 0 0 1 0 4z" fill="#111"/></svg></i>418 Meridian Street - Suite 120,<br>Alder Springs NY, 10987</div>
      <div><i><svg width="12" height="12" viewBox="0 0 12 12"><rect x="1" y="4" width="10" height="7" rx="1" fill="#111"/><rect x="3" y="1" width="6" height="4" fill="#111"/></svg></i>(555) 014-7781</div>
    </div>
  </div>
  <div class="f-col f-sub" style="left:837px">
    <h4>SUBSCRIBE TO OUR BLOG</h4>
    <p>Sign up today to get resources on how to attract and retain more customers!</p>
    <div class="email"><span>Email Address</span><b><svg width="16" height="16" viewBox="0 0 16 16"><path d="M1 7l14-6-5 14-2-6z" fill="#fff"/></svg></b></div>
  </div>
</footer>
<div class="abs chat"><svg width="18" height="16" viewBox="0 0 18 16"><path d="M9 1C4.6 1 1 3.8 1 7.2c0 1.9 1.1 3.6 2.9 4.7L3 15l4-2.2c.6.1 1.300.2 2 .2 4.4 0 8-2.8 8-6.2S13.4 1 9 1z" fill="#fff"/></svg></div>
<div class="abs bottom">
  <div class="abs copy">Copyright© 2025 &nbsp;<u>Haverlock Trial Firm PLLC</u> | &nbsp;All Rights Reserved</div>
  <div class="abs legal">Terms and Conditions &nbsp; | &nbsp; Sitemap</div>
</div>

</body>
</html>
```